Stationery Design Project

I need a stationary design for our company. we are based in Houston, TX and we are called Mira Vell Lending. And we are wanting to brand our MoneyMendPlus program, which includes our tax preparation and restoration, credit repair service. Although our business offers other programs, we are interested in mainly focusing on The MoneyMendPlus program. We are looking for way to brand our ourselves and I believe that a great stationery design will help in achieving this goal. Our logo design is blue and light blue. the slogan is orange.

Industry/Entity Type

Business

Requirements
Must have
• Address: 30871 Calloway Ln. B-22
Houston, TX 75419
Tel. 555-318-6207
Fax 555-294-7153
www.miravelllending.example
info@miravelllending.example
Our Slogan: Happiness, Restored!

```html
<!DOCTYPE html>
<html lang="en">
<head>
<meta charset="utf-8">
<title>MoneyMendPlus Stationery</title>
<link href="https://fonts.googleapis.com/css2?family=Cinzel&family=Open+Sans:wght@400&family=Tinos&display=swap" rel="stylesheet">
<style>
  :root {
    --backdrop: #e9e4da;
    --white: #ffffff;
    --brand-blue: #1a86c8;
    --deep-blue: #1b4a93;
    --sky-blue: #0a97d8;
    --navy: #0f3a64;
    --pale-blue: #cfe5f6;
    --orange: #f5a11c;
    --ink: #2a2a2a;
    --accent-orange: #e8731c;
  }
  * { margin: 0; padding: 0; box-sizing: border-box; }
  html, body { width: 1200px; height: 772px; overflow: hidden; }
  body { background: var(--backdrop); position: relative; font-family: "Open Sans", Arial, sans-serif; }

  .card {
    position: absolute; width: 508px; height: 290px; border-radius: 18px;
    overflow: hidden; box-shadow: 0 3px 8px rgba(0,0,0,0.25);
  }
  .card-front { left: 87px; top: 83px; background: var(--white); }
  .card-back-blue { left: 628px; top: 78px; background: linear-gradient(90deg, var(--sky-blue), var(--deep-blue)); }
  .card-back-pale { left: 84px; top: 403px; background: var(--pale-blue); }
  .card-back-white { left: 632px; top: 403px; background: var(--white); }

  .swoosh { position: absolute; inset: 0; }

  .program-name {
    position: absolute; font-family: "Tinos", "Times New Roman", serif;
    font-size: 42px; color: var(--brand-blue); white-space: nowrap; letter-spacing: -0.5px;
  }
  .card-front .program-name { left: 25px; top: 92px; }
  .card-back-white .program-name { left: 0; right: 0; top: 170px; text-align: center; font-size: 44px; }
  .name-mark {
    position: absolute; width: 22px; height: 22px; background: var(--brand-blue);
  }
  .card-front .name-mark { left: 25px; top: 60px; }
  .card-back-white .name-mark { left: 243px; top: 130px; }

  .contact { position: absolute; left: 28px; font-size: 12.5px; color: var(--ink); line-height: 1; }
  .contact .label { color: var(--accent-orange); }
  .address { top: 158px; }
  .phones { top: 200px; }
  .email { top: 217px; }
  .web { top: 239px; }

  .slogan {
    position: absolute; right: 26px; top: 220px; text-align: right;
    font-family: "Cinzel", Georgia, serif; font-size: 20px; line-height: 26px;
    color: var(--white); letter-spacing: 0.5px;
  }

  .lender-block {
    position: absolute; width: 150px; height: 150px; background: var(--navy);
    border: 4px solid rgba(255,255,255,0.85); outline: 1px solid rgba(0,0,0,0.15);
    display: flex; flex-direction: column; align-items: center; justify-content: center; gap: 14px;
  }
  .card-back-blue .lender-block { left: 180px; top: 52px; }
  .card-back-pale .lender-block { left: 178px; top: 50px; border-color: var(--pale-blue); outline-color: #7a9ab5; }
  .lender-square { width: 28px; height: 28px; background: var(--white); }
  .lender-name {
    font-family: "Tinos", "Times New Roman", serif; font-size: 14px; color: var(--white); white-space: nowrap;
  }

  .site {
    position: absolute; left: 0; right: 0; text-align: center;
    font-size: 12.5px; letter-spacing: 4.6px; white-space: nowrap;
  }
  .card-back-blue .site { top: 240px; color: rgba(255,255,255,0.9); }
  .card-back-pale .site { top: 241px; color: var(--navy); }
  .card-back-white .site { top: 241px; color: var(--navy); }
</style>
</head>
<body>

  <section class="card card-front">
    <svg class="swoosh" viewBox="0 0 508 290" width="508" height="290" aria-hidden="true">
      <path d="M0,266 C170,300 420,230 508,55 L508,290 L0,290 Z" fill="var(--brand-blue)"/>
      <path d="M0,256 C170,292 400,215 490,0 L508,0 L508,55 C420,230 170,300 0,266 Z" fill="var(--orange)"/>
    </svg>
    <span class="name-mark"></span>
    <div class="program-name">MoneyMendPlus</div>
    <p class="contact address">30871 Calloway Ln. B-22, Houston, TX 75419</p>
    <p class="contact phones"><span class="label">T:</span> 555-318-6207, <span class="label">F:</span> 555-294-7153</p>
    <p class="contact email"><span class="label">E:</span> info@miravelllending.example</p>
    <p class="contact web">www.miravelllending.example</p>
    <p class="slogan">HAPPINESS,<br>RESTORED!</p>
  </section>

  <section class="card card-back-blue">
    <div class="lender-block">
      <span class="lender-square"></span>
      <span class="lender-name">Mira Vell Lending</span>
    </div>
    <p class="site">www.miravelllending.example</p>
  </section>

  <section class="card card-back-pale">
    <div class="lender-block">
      <span class="lender-square"></span>
      <span class="lender-name">Mira Vell Lending</span>
    </div>
    <p class="site">www.miravelllending.example</p>
  </section>

  <section class="card card-back-white">
    <span class="name-mark"></span>
    <div class="program-name">MoneyMendPlus</div>
    <p class="site">www.miravelllending.example</p>
  </section>

</body>
</html>
```